New Business Card Design Project

Use the flyer uploaded and website www.brightoakbuilders.com for inspiration.
List Our Services on Backside of business cards
Marcus Delling
Harborline Builders Inc.
Licensed General Contractors
858-471-6093

Contact Information for Business Card

Use the flyer uploaded and website www.brightoakbuilders.com for inspiration. List Our Services on Backside of business cards Marcus Delling Harborline Builders Inc. Licensed General Contractors 858-471-6093

```html
<!DOCTYPE html>
<html lang="en">
<head>
<meta charset="utf-8">
<title>Harborline Builders — Business Cards</title>
<link href="https://fonts.googleapis.com/css2?family=Montserrat:wght@400;500;700&display=swap" rel="stylesheet">
<style>
  :root {
    --stage: #2b2b2b;
    --card: #1d1d1d;
    --ink: #f2f2f2;
    --ink-soft: #cfcfcf;
    --band: #f4f4f4;
    --band-ink: #1d1d1d;
    --rule: #8a8a8a;
  }
  * { box-sizing: border-box; margin: 0; padding: 0; }
  html, body { width: 1200px; height: 875px; overflow: hidden; }
  body {
    background: var(--stage);
    font-family: "Montserrat", sans-serif;
    color: var(--ink);
    position: relative;
  }
  .card {
    position: absolute;
    width: 560px;
    height: 320px;
    background: var(--card);
    border-radius: 22px;
    overflow: hidden;
  }
  .card--back { left: 60px; top: 90px; }
  .card--front { left: 580px; top: 450px; }

  .brand {
    display: flex;
    align-items: center;
    justify-content: center;
    gap: 12px;
    font-weight: 500;
    font-size: 24px;
    letter-spacing: 3px;
    text-transform: uppercase;
    color: var(--ink);
  }
  .brand__mark {
    width: 14px; height: 14px;
    border: 1.5px solid var(--ink);
    border-radius: 50%;
  }

  /* back side */
  .card--back .brand { margin-top: 62px; }
  .services { text-align: center; margin-top: 30px; }
  .services__title {
    display: inline-block;
    font-weight: 700;
    font-size: 17px;
    padding-bottom: 6px;
    border-bottom: 1px solid var(--ink);
    margin-bottom: 22px;
  }
  .services__list {
    list-style: none;
    font-size: 11.5px;
    line-height: 2;
    color: var(--ink-soft);
  }
  .services__list li span + span::before { content: "•"; margin: 0 8px; }

  /* front side */
  .card--front .brand { margin-top: 78px; }
  .details {
    position: absolute;
    left: 0; right: 0; top: 172px;
    display: flex;
    justify-content: center;
    align-items: center;
  }
  .person { text-align: right; padding-right: 18px; }
  .person__name { font-weight: 700; font-size: 21px; }
  .person__role { font-size: 12px; color: var(--ink-soft); margin-top: 2px; }
  .divider { width: 1px; height: 66px; background: var(--rule); }
  .contact { list-style: none; padding-left: 18px; font-size: 12px; }
  .contact li { display: flex; align-items: center; gap: 10px; line-height: 22px; }
  .contact svg { width: 12px; height: 12px; fill: var(--ink); }
  .license-band {
    position: absolute;
    left: 0; right: 0; bottom: 0;
    height: 52px;
    background: var(--band);
    color: var(--band-ink);
    font-size: 13px;
    display: flex;
    align-items: center;
    justify-content: center;
  }
</style>
</head>
<body>
  <section class="card card--back" aria-label="Business card back">
    <div class="brand"><span class="brand__mark"></span>Harborline Builders</div>
    <div class="services">
      <h2 class="services__title">Our Services</h2>
      <ul class="services__list">
        <li><span>Remodel: Kitchen &amp; Bath</span><span>Painting: Interior &amp; Exterior</span><span>Flooring: Carpet, Vinyl, Wood</span></li>
        <li><span>Window: Door Replacement</span><span>Plumbing: Repair &amp; Upgrades</span><span>Energy Efficient Upgrades</span></li>
        <li><span>Deck &amp; Patio Construction</span><span>Water &amp; Mold Damage</span><span>Garage Renovation</span></li>
      </ul>
    </div>
  </section>

  <section class="card card--front" aria-label="Business card front">
    <div class="brand"><span class="brand__mark"></span>Harborline Builders</div>
    <div class="details">
      <div class="person">
        <p class="person__name">Marcus Delling</p>
        <p class="person__role">Managing Director</p>
      </div>
      <div class="divider"></div>
      <ul class="contact">
        <li><svg viewBox="0 0 24 24"><path d="M6.6 10.8a15 15 0 0 0 6.6 6.6l2.2-2.2a1 1 0 0 1 1-.25 11.4 11.4 0 0 0 3.6.6 1 1 0 0 1 1 1V20a1 1 0 0 1-1 1A17 17 0 0 1 3 4a1 1 0 0 1 1-1h3.5a1 1 0 0 1 1 1 11.4 11.4 0 0 0 .6 3.6 1 1 0 0 1-.25 1z"/></svg>858-471-6093</li>
        <li><svg viewBox="0 0 24 24"><path d="M2 5h20v14H2z M2 5l10 8 10-8" stroke="#1d1d1d" stroke-width="1.5"/></svg>info@brightoakbuilders.com</li>
        <li><svg viewBox="0 0 24 24"><circle cx="12" cy="12" r="10"/></svg>www.brightoakbuilders.com</li>
      </ul>
    </div>
    <div class="license-band">CSLB Licensed No. #1048265</div>
  </section>
</body>
</html>
```